Lotus Ridge Website

We need a website that has clean, asian looking images that relax and motivate people to come into our integrated medical center. My current website is www.needlecalmharbor.com and I would like the design for Lotus Ridge Wellness Partners to be similar but more inviting with video content and a product purchase store as well. A moving banner would be nice too. When people are looking for ways of losing weight or getting out of pain we want them to make the connection that we have the solution. This website needs to provide sufficient information so that patients are well informed and choose us as their health provider before they ever walk through our doors. We offer comprehensive natural medicine that is based on the principles that the body can heal itself when given the right conditions. Our services include medical weight loss and hormone balancing, acupuncture and chinese herbal medicine, physical medicine, trigger point injections, allergy testing and joint rehabilitation. The Medical Doctor and Licensed Acupuncturist work as a team to provide optimal care that is catered to each individual who comes through our doors.
Updates

Target Market(s)

40 to 50 year olds who want to lose weight or have pain issues.

Industry/Entity Type

Medical

Requirements
Must have
• Use photos from our website www.needlecalmharbor.com or similar content. Video content. Moving banner with relaxing images.
Nice to have
• Happy, healthy looking people. Medical Doctors working as a team. Friendly staff in a cutting edge facility.
Should not have
• Papyrus font, or big bold words.

```html
<!DOCTYPE html>
<html lang="en">
<head>
<meta charset="utf-8">
<title>Lotus Ridge Wellness Partners – Contact</title>
<link rel="stylesheet" href="https://fonts.googleapis.com/css2?family=Maven+Pro:wght@400;500;700&display=swap">
<style>
:root{
  --header-bg:#f2ede4;
  --panel-top:#cdbd9d;
  --panel-bottom:#e3d8c3;
  --brand-box:#9d9a78;
  --brand-text:#f3efe2;
  --light-bg:#efe9df;
  --footer-bg:#857467;
  --footer-text:#f1e9df;
  --contact-box:#c8c0a2;
  --ink:#6b5a4a;
  --ink-soft:#857362;
  --field-bg:#efe8da;
  --field-line:#b9aa8c;
  --nav:#a6957f;
  --icon-bg:#cfc3b0;
  --social:#5e534b;
}
*{box-sizing:border-box;margin:0;padding:0}
html,body{width:1000px;height:1200px;overflow:hidden}
body{position:relative;font-family:"Maven Pro",sans-serif;color:var(--ink);background:var(--light-bg)}
.abs{position:absolute}

/* header */
.site-header{left:0;top:0;width:1000px;height:74px;background:var(--header-bg);border-bottom:1px solid #cbbfa9}
.main-nav{right:131px;top:46px;display:flex;gap:22px;font-size:10px;font-weight:700;letter-spacing:1.2px;color:var(--nav)}
.main-nav .current{color:var(--ink);border-bottom:1px solid var(--ink);padding-bottom:2px}
.nav-pointer{left:838px;top:67px;width:0;height:0;border-left:7px solid transparent;border-right:7px solid transparent;border-bottom:7px solid var(--panel-top)}

/* contact panel */
.contact-panel{left:0;top:74px;width:1000px;height:487px;background:linear-gradient(var(--panel-top),var(--panel-bottom));box-shadow:inset 0 6px 8px rgba(0,0,0,.08)}
.brand-box{left:131px;top:56px;width:175px;height:235px;background:var(--brand-box);box-shadow:0 3px 10px rgba(0,0,0,.18);display:flex;flex-direction:column;align-items:center;justify-content:center;gap:12px}
.brand-mark{width:26px;height:26px;background:var(--brand-text)}
.brand-name{font-size:24px;font-weight:700;color:var(--brand-text);text-align:center;line-height:1.1}
.brand-tab{left:122px;top:56px;border-left:9px solid transparent;border-bottom:14px solid #6f6e48}
.intro{left:131px;top:327px;width:180px;font-size:11px;line-height:19px;color:var(--ink)}
.intro p+p{margin-top:19px}
.divider{border-left:2px dotted #9c8b73}

.radio-row{left:381px;top:130px;display:flex;gap:24px;font-size:11px;font-weight:500}
.radio{display:flex;align-items:center;gap:6px}
.radio i{width:19px;height:19px;border-radius:50%;background:var(--field-bg);border:1px solid var(--field-line);display:flex;align-items:center;justify-content:center}
.radio.on i::after{content:"";width:7px;height:7px;border-radius:50%;background:var(--ink)}
.label{font-size:10px;font-weight:700;color:var(--ink)}
.field{height:20px;background:var(--field-bg);border:1px solid var(--field-line);border-radius:2px;box-shadow:inset 0 1px 2px rgba(0,0,0,.08)}
.select{font-size:10px;font-weight:700;padding:4px 7px;display:flex;justify-content:space-between}
.select b{width:18px;border-left:1px solid var(--field-line);margin:-4px -7px -4px 0;display:flex;align-items:center;justify-content:center}
.select b::after{content:"";border-left:4px solid transparent;border-right:4px solid transparent;border-top:5px solid var(--ink)}
.button{height:25px;border-radius:7px;background:linear-gradient(#fbf8f2,#e9e1d2);border:1px solid #b9ab93;box-shadow:0 2px 3px rgba(0,0,0,.2);font-size:11px;font-weight:700;letter-spacing:1.2px;color:var(--ink);display:flex;align-items:center;justify-content:center}

/* info band */
.info-band{left:0;top:561px;width:1000px;height:376px;background:repeating-linear-gradient(var(--light-bg) 0 44px,#e8e1d5 44px 45px)}
.small-brand{left:131px;top:614px;display:flex;align-items:center;gap:10px}
.small-brand .brand-mark{width:24px;height:24px;background:var(--ink-soft)}
.small-brand span{font-size:20px;font-weight:700;color:var(--ink-soft)}
.text{font-size:11px;line-height:17px;color:var(--ink)}
.icon{width:28px;height:28px;border-radius:50%;background:var(--icon-bg);display:flex;align-items:center;justify-content:center}
.map{left:631px;top:638px;width:238px;height:224px;background:linear-gradient(135deg,#ecebe4,#dcdad0);border:1px solid #a9a59a}

/* footer */
.site-footer{left:0;top:937px;width:1000px;height:224px;background:var(--footer-bg)}
.footer-col{font-size:9px;line-height:19px;color:var(--footer-text)}
.footer-col .head{font-weight:700}
.footer-col .rule{border-top:1px dotted #c4b6a8;margin:4px 0 6px;width:110px}
.calligraphy{left:544px;top:956px;width:40px;height:177px;background:linear-gradient(#7b6b5f,#76665a);opacity:.8}
.contact-box{left:631px;top:919px;width:238px;height:150px;background:var(--contact-box);box-shadow:0 3px 8px rgba(0,0,0,.25);padding:12px 13px;color:var(--ink)}
.contact-tab{left:620px;top:919px;border-left:11px solid transparent;border-bottom:14px solid #aea688}
.contact-box h2{font-size:17px;font-weight:700}
.contact-box p{font-size:10px;line-height:18px;margin-top:2px}
.contact-line{display:flex;align-items:center;gap:6px;font-size:12px;font-weight:700;margin-top:6px}
.social{top:1092px;width:28px;height:28px;border-radius:50%;background:var(--social)}
.bottom-bar{left:0;top:1161px;width:1000px;height:39px;background:var(--header-bg);border-top:1px solid #cdbfae;font-size:10px;padding:12px 131px;color:var(--ink)}
</style>
</head>
<body>

<header class="site-header abs">
  <nav class="main-nav abs">
    <span>HOME</span><span>ABOUT US</span><span>ACUPUNCTURE</span><span>HEALTHCARE</span><span>SHOP</span><span class="current">CONTACT</span>
  </nav>
</header>

<section class="contact-panel abs">
  <div class="brand-tab abs"></div>
  <div class="brand-box abs">
    <div class="brand-mark"></div>
    <div class="brand-name">Lotus Ridge</div>
  </div>
  <div class="intro abs">
    <p>Concupis plusque in insupinaria detriment est quam in his et rebus emolument oariunt iniur.</p>
    <p>Itaque ne iustitial dem rect quis dixer per se ipsad optabil, sed quiran cunditat vel pluify to factor tum poen legum odio et nebevol.</p>
  </div>
  <div class="divider abs" style="left:343px;top:37px;height:409px"></div>

  <form>
    <div class="radio-row abs" style="top:56px">
      <span class="radio on"><i></i>Mrs.</span>
      <span class="radio"><i></i>Mr.</span>
    </div>
    <span class="label abs" style="left:381px;top:98px">First Name :</span>
    <span class="label abs" style="left:637px;top:98px">Name :</span>
    <div class="field abs" style="left:381px;top:113px;width:231px"></div>
    <div class="field abs" style="left:637px;top:113px;width:232px"></div>
    <span class="label abs" style="left:381px;top:155px">E-mail :</span>
    <span class="label abs" style="left:637px;top:155px">Telephone :</span>
    <div class="field abs" style="left:381px;top:169px;width:231px"></div>
    <div class="field abs" style="left:637px;top:169px;width:232px"></div>
    <div class="field select abs" style="left:381px;top:207px;width:231px">Select subject<b></b></div>
    <span class="label abs" style="left:381px;top:248px">Message :</span>
    <div class="field abs" style="left:381px;top:263px;width:488px;height:113px"></div>
    <div class="button abs" style="left:716px;top:426px;width:71px">CANCEL</div>
    <div class="button abs" style="left:798px;top:426px;width:71px">SUBMIT</div>
  </form>
</section>

<section class="info-band abs">
  <div class="small-brand abs" style="top:53px">
    <div class="brand-mark"></div><span>Lotus Ridge</span>
  </div>
  <p class="text abs" style="left:131px;top:139px;line-height:19px">18 Cedar Lane Suite 210<br>Maple Falls</p>
  <div class="icon abs" style="left:131px;top:197px">
    <svg width="14" height="14" viewBox="0 0 14 14"><circle cx="7" cy="7" r="6" fill="none" stroke="#857362" stroke-width="1.5"/><path d="M7 3.5V7h2.5" fill="none" stroke="#857362" stroke-width="1.5"/></svg>
  </div>
  <p class="text abs" style="left:167px;top:203px;width:150px;line-height:14px">Monday to friday from 8 a.m. to 6 p.m.</p>
  <div class="icon abs" style="left:131px;top:253px">
    <svg width="14" height="14" viewBox="0 0 14 14"><rect x="2" y="1.5" width="10" height="11" fill="none" stroke="#857362" stroke-width="1.4"/><path d="M4.5 5h5M4.5 7.5h5M4.5 10h3" stroke="#857362" stroke-width="1.2"/></svg>
  </div>
  <p class="text abs" style="left:167px;top:260px;width:150px;line-height:13px">We look forward to meeting you and helping you in your healing process.</p>
  <div class="divider abs" style="left:343px;top:78px;height:219px"></div>

  <div class="icon abs" style="left:381px;top:85px">
    <svg width="12" height="16" viewBox="0 0 12 16"><rect x="2" y="1" width="8" height="14" rx="1.5" fill="none" stroke="#857362" stroke-width="1.5"/><rect x="4" y="3.5" width="4" height="4" fill="#857362"/></svg>
  </div>
  <p class="text abs" style="left:417px;top:92px">Tel : +1 (555) 204 1187</p>
  <div class="icon abs" style="left:381px;top:142px">
    <svg width="14" height="14" viewBox="0 0 14 14"><rect x="1.5" y="5" width="11" height="7" rx="1" fill="#857362"/><rect x="4" y="1.5" width="6" height="4" fill="none" stroke="#857362" stroke-width="1.3"/></svg>
  </div>
  <p class="text abs" style="left:417px;top:149px">Fax: +1 (555) 204 1188</p>
  <div class="icon abs" style="left:381px;top:197px">
    <svg width="14" height="12" viewBox="0 0 14 12"><rect x="1" y="1" width="12" height="10" rx="1" fill="#857362"/><path d="M1.5 2l5.5 4.5L12.5 2" fill="none" stroke="#cfc3b0" stroke-width="1.2"/></svg>
  </div>
  <p class="text abs" style="left:417px;top:203px;line-height:25px">info@lotusridgewell.com<br>visit@lotusridgewell.com</p>

  <div class="map abs" style="top:77px" role="img" aria-label="Street map showing the clinic location"></div>
</section>

<footer class="site-footer abs">
  <div class="footer-col abs" style="left:131px;top:28px">
    <div class="head">• HOME</div>
    <div class="rule"></div>
    <div class="head">• ABOUT US</div>
    <div>• Philosophy</div>
    <div>• Our team</div>
  </div>
  <div class="footer-col abs" style="left:257px;top:28px">
    <div class="head">• ACUPUNCTURE</div>
    <div>• Information</div>
    <div>• History</div>
    <div>• Seitai Shinpo</div>
    <div class="rule"></div>
    <div class="head">• HEALTHCARE</div>
    <div>• Programme</div>
    <div>• So Tai Ho</div>
    <div>• Therapy</div>
  </div>
  <div class="footer-col abs" style="left:382px;top:28px">
    <div class="head">• SHOP</div>
    <div>• Massage Oil</div>
    <div>• Therapeutics</div>
    <div>• Herbal</div>
    <div>• Beauty products</div>
    <div class="rule"></div>
    <div class="head">• CONTACT</div>
  </div>
</footer>
<div class="calligraphy abs" role="img" aria-label="Vertical Chinese calligraphy for health and happiness"></div>

<div class="contact-tab abs"></div>
<aside class="contact-box abs">
  <h2>Contact us</h2>
  <p>Lorem ipsum do pland sit amet, con sectetur a dip sching.</p>
  <div class="contact-line">
    <svg width="12" height="18" viewBox="0 0 12 18"><rect x="1.5" y="1" width="9" height="16" rx="1.5" fill="none" stroke="#6b5a4a" stroke-width="1.6"/><rect x="3.5" y="3.5" width="5" height="5" fill="#6b5a4a"/></svg>
    (555) 630-4412
  </div>
  <div class="contact-line">
    <svg width="14" height="12" viewBox="0 0 14 12"><rect x="1" y="1" width="12" height="10" rx="1" fill="#6b5a4a"/><path d="M1.5 2l5.5 4.5L12.5 2" fill="none" stroke="#c8c0a2" stroke-width="1.2"/></svg>
    info@lotusridgewell.com
  </div>
</aside>

<span class="social abs" style="left:714px" aria-label="Social network"></span>
<span class="social abs" style="left:756px" aria-label="Social network"></span>
<span class="social abs" style="left:798px" aria-label="Social network"></span>
<span class="social abs" style="left:840px" aria-label="Social network"></span>

<div class="bottom-bar abs">© Copyright Lotus Ridge Wellness 2012 - Privacy policy</div>

</body>
</html>
```